Social Media App Needs PPT Template

We need a PowerPoint template for a new social media company based in the DC area called "Bold Ledger." We provide an interactive digital platform for executives to share actionable advice. We would like to see designs that use our orange logo color as an accent, but are mainly grey, white, and black. The final design should communicate clean, chic, modern, and professional.

Target Market(s)

Executives

Industry/Entity Type

Information Technology

Font styles to use
Sans Serif

Colors
f78f20
fbe7d2
ffffff
000000
e8e8e8
757575

Requirements
Must have
• My project must have title page and many options for the body of the ppt (graphs, tables, etc). It also needs to be easy to modify. I must have someone who is experienced in creating powerpoint templates.
Nice to have
• It would be nice to have a very modern and clean design that includes the logo on every page, but still leaves a lot of room for the content of the slide
Should not have
• My design project should not look to busy.

```html
<!DOCTYPE html>
<html lang="en">
<head>
<meta charset="utf-8">
<title>Bold Ledger – Content Slide</title>
<link href="https://fonts.googleapis.com/css2?family=Lato:wght@300;400;700&display=swap" rel="stylesheet">
<style>
  :root {
    --backdrop: #939393;
    --slide-bg: #f7f7f7;
    --orange: #f78f20;
    --orange-deep: #e8841c;
    --charcoal: #464646;
    --text: #3f3f3f;
    --placeholder: #cdcecf;
    --placeholder-text: #e1e2e3;
    --white: #ffffff;
  }
  * { margin: 0; padding: 0; box-sizing: border-box; }
  html, body {
    width: 1200px; height: 960px; overflow: hidden;
    background: var(--backdrop);
    font-family: "Lato", Arial, sans-serif;
  }
  .page-label {
    position: absolute; top: 44px; left: 0; width: 1200px;
    text-align: center; color: var(--white);
    font-weight: 300; font-size: 25px;
  }
  .slide {
    position: absolute; left: 87px; top: 128px;
    width: 1046px; height: 784px;
    background: radial-gradient(ellipse at 50% 45%, #ffffff 0%, var(--slide-bg) 60%, #efefef 100%);
    overflow: hidden;
  }
  .slide-frame { position: absolute; inset: 0; }
  .slide-title {
    position: absolute; left: 31px; top: 70px;
    color: var(--white); font-weight: 300; font-size: 39px; line-height: 1;
  }
  .brand-name {
    position: absolute; left: 820px; top: 49px; width: 226px; height: 81px;
    display: flex; align-items: center; justify-content: center;
    color: var(--white); font-weight: 700; font-size: 26px; letter-spacing: 1px;
  }
  .media-placeholder {
    position: absolute; left: 62px; top: 201px; width: 429px; height: 269px;
    background: var(--placeholder);
    display: flex; align-items: center; justify-content: center;
    color: var(--placeholder-text); font-weight: 300; font-size: 32px;
  }
  .body-copy {
    position: absolute; left: 63px; top: 510px; width: 436px;
    color: var(--text); font-size: 20px; line-height: 24.4px;
    text-align: justify;
  }
  .key-points {
    position: absolute; left: 561px; top: 232px; width: 450px;
    list-style: none;
  }
  .key-points li {
    position: relative; padding-left: 28px; width: 440px;
    color: var(--text); font-size: 21px; line-height: 31.2px;
    margin-bottom: 31.4px;
  }
  .key-points li::before {
    content: ""; position: absolute; left: 0; top: 11px;
    width: 10px; height: 10px; background: var(--orange);
  }
  .footer-text {
    position: absolute; left: 28px; top: 742px; height: 31px;
    display: flex; align-items: center;
    color: #e4e4e4; font-size: 13.7px;
  }
  .footer-text .divider { margin: 0 8px; }
</style>
</head>
<body>
  <div class="page-label">Page 4</div>

  <section class="slide">
    <svg class="slide-frame" width="1046" height="784" viewBox="0 0 1046 784" aria-hidden="true">
      <defs>
        <linearGradient id="bandGradient" x1="0" y1="0" x2="1" y2="0">
          <stop offset="0" stop-color="#e67e18"/>
          <stop offset="0.8" stop-color="#ec8a1f"/>
          <stop offset="1" stop-color="#f1952a"/>
        </linearGradient>
      </defs>
      <polygon points="0,49 793,49 707,130 0,130" fill="url(#bandGradient)"/>
      <polygon points="560,49 720,49 655,115 540,115" fill="#f09426" opacity="0.35"/>
      <polygon points="0,136 705,136 694,145 0,145" fill="var(--charcoal)"/>
      <polygon points="801,49 1046,49 1046,130 713,130" fill="var(--charcoal)"/>
      <polygon points="814,34 1046,34 1046,44 805,44" fill="var(--orange-deep)"/>
      <polygon points="0,742 298,742 266,773 0,773" fill="var(--charcoal)"/>
      <polygon points="305,742 1046,742 1046,773 273,773" fill="var(--orange-deep)"/>
    </svg>

    <h1 class="slide-title">Title Goes Here</h1>
    <div class="brand-name">Bold Ledger</div>

    <div class="media-placeholder" role="img" aria-label="Image placeholder for slide content">Image Goes Here</div>

    <p class="body-copy">Duis autem vel eum iriure dolor in hendrerit in vulputate velit esse molestie consequat, vel illum dolore eu feugiat nulla facilisis at vero eros et accumsan et iusto odio dignissim qui blandit praesent luptatum zzril delenit augue duis dolore te feugait nulla facilisi.</p>

    <ul class="key-points">
      <li>Souvlaki ignitus carborundum e pluribus unum.</li>
      <li>Defacto lingo est igpay atinlay. Marquee selectus non provisio.</li>
      <li>Quote meon an estimate et non interruptus stadium.</li>
      <li>Sic tempus fugit esperanto hiccup estrogen.</li>
      <li>Epsum factorial non deposit quid pro quo hic escorol.</li>
    </ul>

    <div class="footer-text">www.boldledger.com<span class="divider">|</span>Page 2</div>
  </section>
</body>
</html>
```